Business Card Design for Software Development Company

I am looking for a business card design the incorporates my new logo (attached below).

Key information to include:
Name: Martin Quelbrook
Title: CEO
Email: martin@brightwellcivic.example
Phone: 555-218-9403
Website: www.brightwellcivic.example

NOTE: This design should be easy to edit so that we can order cards for different members of our team.

```html
<!DOCTYPE html>
<html lang="en">
<head>
<meta charset="utf-8">
<title>BrightwellLabs Business Card</title>
<link href="https://fonts.googleapis.com/css2?family=Montserrat:wght@400;600;700&display=swap" rel="stylesheet">
<style>
  :root {
    --backdrop: #1b1b1b;
    --card: #f4f4f4;
    --ink: #222222;
    --teal: #14a898;
    --orange: #e3782a;
  }
  html, body {
    margin: 0;
    padding: 0;
    width: 1200px;
    height: 1059px;
    overflow: hidden;
    background: var(--backdrop);
    font-family: "Montserrat", sans-serif;
    color: var(--ink);
  }
  .canvas {
    position: relative;
    width: 1200px;
    height: 1059px;
  }
  .card {
    position: absolute;
    background: var(--card);
    border-radius: 18px;
  }
  .card--front { left: 257px; top: 89px; width: 687px; height: 390px; }
  .card--back  { left: 254px; top: 547px; width: 693px; height: 393px; }

  .brand {
    position: absolute;
    display: flex;
    flex-direction: column;
    align-items: flex-end;
  }
  .brand__row {
    display: flex;
    align-items: center;
    gap: 10px;
  }
  .brand__mark {
    background: var(--teal);
    flex: none;
  }
  .brand__name {
    font-weight: 700;
    letter-spacing: -1px;
    line-height: 1;
    color: var(--ink);
  }
  .brand__tagline {
    font-weight: 600;
    text-transform: uppercase;
    letter-spacing: 0.3px;
    color: var(--ink);
  }
  .card--front .brand { left: 128px; top: 80px; width: 428px; }
  .card--front .brand__mark { width: 40px; height: 40px; }
  .card--front .brand__name { font-size: 54px; }
  .card--front .brand__tagline { font-size: 6.5px; margin-top: 2px; }

  .card--back .brand { left: 90px; top: 157px; width: 514px; }
  .card--back .brand__mark { width: 48px; height: 48px; }
  .card--back .brand__name { font-size: 65px; }
  .card--back .brand__tagline { font-size: 8px; margin-top: 3px; }

  .person {
    position: absolute;
    right: 368px;
    top: 259px;
    text-align: right;
  }
  .person__name {
    font-size: 26px;
    font-weight: 700;
    letter-spacing: 0.3px;
    line-height: 1.1;
    white-space: nowrap;
  }
  .person__first { color: var(--teal); }
  .person__last { color: var(--orange); }
  .person__title {
    font-size: 17px;
    font-weight: 400;
    margin-top: 1px;
  }
  .divider {
    position: absolute;
    left: 343px;
    top: 251px;
    width: 1px;
    height: 66px;
    background: var(--teal);
  }
  .contacts {
    position: absolute;
    left: 368px;
    top: 244px;
    margin: 0;
    padding: 0;
    list-style: none;
  }
  .contacts__item {
    display: flex;
    align-items: center;
    gap: 7px;
    height: 28px;
    font-size: 17px;
    letter-spacing: 0.3px;
    white-space: nowrap;
  }
  .contacts__icon { width: 11px; height: 11px; flex: none; }
</style>
</head>
<body>
<div class="canvas">

  <section class="card card--front">
    <div class="brand">
      <div class="brand__row">
        <span class="brand__mark"></span>
        <span class="brand__name">BrightwellLabs</span>
      </div>
      <span class="brand__tagline">A division of Brightwell Civic</span>
    </div>

    <div class="person">
      <div class="person__name"><span class="person__first">Martin</span> <span class="person__last">Quelbrook</span></div>
      <div class="person__title">CEO</div>
    </div>

    <div class="divider"></div>

    <ul class="contacts">
      <li class="contacts__item">
        <svg class="contacts__icon" viewBox="0 0 12 12" aria-hidden="true"><path d="M1 4 Q6 0 11 4 L9 5 L8 4 Q6 3 4 4 L3 5 Z M3 6 H9 L10 11 H2 Z" fill="var(--orange)"/></svg>
        555-218-9403
      </li>
      <li class="contacts__item">
        <svg class="contacts__icon" viewBox="0 0 12 12" aria-hidden="true"><path d="M1 5 L6 1 L11 5 V11 H1 Z" fill="var(--orange)"/><path d="M1 5 L6 8.5 L11 5" fill="none" stroke="#fff" stroke-width="1"/></svg>
        martin@brightwellcivic.example
      </li>
      <li class="contacts__item">
        <svg class="contacts__icon" viewBox="0 0 12 12" aria-hidden="true"><circle cx="6" cy="6" r="5.5" fill="var(--orange)"/><path d="M3 3 Q5 4 4 6 Q6 7 5 10 M8 2 Q7 4 9 5" fill="none" stroke="#fff" stroke-width="1"/></svg>
        www.brightwellcivic.example
      </li>
    </ul>
  </section>

  <section class="card card--back">
    <div class="brand">
      <div class="brand__row">
        <span class="brand__mark"></span>
        <span class="brand__name">BrightwellLabs</span>
      </div>
      <span class="brand__tagline">A division of Brightwell Civic</span>
    </div>
  </section>

</div>
</body>
</html>
```